Website for designing and selling name-labels

We are looking for a fresh design for a site similar to these (www.tovskrabe.no, www.dremsgard.no, www.kvalbuffo.no) where the consumer can come online designing their own labels (30x15 mm) , either with onlye text or with text, choose a pre-defined symbol (which we have) and/or a color. We will the print the labels on our side, and send it to the customer.

We are looking for the front page, product page and check out - page.

Target Market(s)

families with childring, scools, kinder garden, industry

Number of Pages Required

3 page

Requirements
Nice to have
• bright and easy design
easy to design and see their own designs
easy check out - few steps

```html
<!DOCTYPE html>
<html lang="en">
<head>
<meta charset="utf-8">
<title>Tagglunden.no – Design your own name tags</title>
<link href="https://fonts.googleapis.com/css2?family=Archivo:wght@400;500;600;700&family=Lato:wght@400;700&display=swap" rel="stylesheet">
<style>
:root{
  --teal:#1a9688;
  --teal-dark:#147d72;
  --ink:#111111;
  --muted:#555555;
  --white:#ffffff;
  --footer:#0c0c0c;
  --line:#3a3a3a;
  --star:#1fa67a;
}
*{box-sizing:border-box;margin:0;padding:0}
html,body{width:1200px;height:2859px;overflow:hidden}
body{position:relative;font-family:"Archivo",sans-serif;color:var(--ink);background:var(--white)}
.abs{position:absolute}

.promo-bar{left:0;top:0;width:1200px;height:47px;background:var(--teal);color:var(--white);font-size:15px;display:flex;align-items:center;justify-content:center}

.site-header{left:0;top:47px;width:1200px;height:72px}
.brand{left:112px;top:9px;height:53px;display:flex;align-items:center;gap:8px;font-weight:700;font-size:22px;color:var(--ink)}
.brand-mark{width:14px;height:14px;background:var(--teal)}
.main-nav{left:325px;top:0;height:72px;display:flex;align-items:center;gap:18px;font-size:14.5px;font-weight:500;white-space:nowrap}
.header-icons{left:1002px;top:20px;display:flex;gap:18px;align-items:center}
.cart-count{position:absolute;right:-6px;top:-6px;width:15px;height:15px;border-radius:50%;background:var(--teal);color:#fff;font-size:10px;text-align:center;line-height:15px}

.hero{left:0;top:119px;width:1200px;height:598px;background:linear-gradient(100deg,#e9a317 0%,#f0b21c 45%,#f6c226 70%,#eab22a 100%)}
.hero-photo-tones{left:0;top:0;width:520px;height:598px;background:radial-gradient(ellipse at 40% 55%,rgba(70,160,210,.55),rgba(240,180,30,0) 70%)}
.hero-title{left:643px;top:196px;font-size:49px;font-weight:700;line-height:50px;color:#f3efe4;letter-spacing:-.5px}
.hero-text{left:643px;top:299px;width:450px;font-size:16.5px;line-height:29px;color:#fbf1d2}
.hero-btn{left:645px;top:375px;width:137px;height:42px;border:1.5px solid #fff;border-radius:3px;color:#fff;font-size:16px;font-weight:500;display:flex;align-items:center;justify-content:center}
.hero-arrow{top:280px;width:38px;height:38px;border:2px solid #fff;border-radius:50%}
.hero-dots{left:565px;top:549px;display:flex;gap:9px}
.hero-dots span{width:11px;height:11px;border-radius:50%;background:rgba(255,255,255,.6)}
.hero-dots span:first-child{background:#fff}

.rating-summary{left:112px;top:768px;width:188px;text-align:center}
.rating-summary h3{font-size:27px;font-weight:500}
.stars{display:flex;gap:3px;justify-content:center;margin:8px 0}
.rating-summary p{font-size:13.5px}
.review-brand{margin-top:14px;font-size:21px;font-weight:500;display:flex;align-items:center;justify-content:center;gap:6px}
.review-brand i{width:14px;height:14px;border-radius:50%;background:var(--star);display:inline-block}
.review{top:776px;width:210px}
.review .top{display:flex;justify-content:space-between;align-items:center}
.review .top small{font-size:11.5px;color:#444}
.review h4{font-size:16px;font-weight:600;margin-top:12px}
.review p{font-size:13px;color:var(--muted);line-height:24px;margin-top:8px}
.review b{display:block;font-size:15px;font-weight:600;margin-top:10px}

.product-tile{width:316px;height:298px;overflow:hidden}
.tile-caption{position:absolute;left:0;bottom:0;width:100%;height:70px;background:rgba(255,255,255,.55);padding:20px 10px 0}
.tile-caption h5{font-size:16px;font-weight:600}
.tile-caption p{font-size:13px;margin-top:3px}
.tile-btn{position:absolute;right:12px;bottom:17px;width:112px;height:34px;background:var(--teal);color:#fff;border-radius:2px;font-size:14px;font-weight:500;display:flex;align-items:center;justify-content:center}

.faq-photo{left:0;top:1682px;width:600px;height:494px;background:linear-gradient(120deg,#8aa7b8 0%,#e9c77b 35%,#d46a78 60%,#f0d57a 85%,#c6dbe5 100%)}
.faq{left:600px;top:1682px;width:600px;height:494px;background:var(--teal)}
.faq h2{position:absolute;left:40px;top:82px;font-size:27px;font-weight:700;color:#fff;letter-spacing:-.3px}
.faq-item{position:absolute;left:42px;width:446px;height:44px;background:#fff;border-radius:3px;font-size:13.5px;padding:0 16px;display:flex;align-items:center;justify-content:space-between}

.testimonial{top:2260px;width:312px;text-align:center;font-family:"Lato",sans-serif}
.testimonial p{font-size:15.5px;line-height:25px;color:#333;margin-top:12px}
.testimonial b{display:block;font-size:16px;margin-top:15px;color:#111}

.site-footer{left:0;top:2520px;width:1200px;height:339px;background:var(--footer);color:#fff;font-family:"Lato",sans-serif}
.footer-brand{left:113px;top:70px;height:58px;display:flex;align-items:center;gap:8px;font-family:"Archivo",sans-serif;font-weight:700;font-size:22px;color:#fff}
.socials{left:130px;top:168px;display:flex;gap:4px}
.socials span{width:30px;height:30px;border:1.5px solid #fff;border-radius:50%}
.footer-col h6{font-family:"Archivo",sans-serif;font-size:19.5px;font-weight:500;margin-bottom:6px}
.footer-col li{list-style:none;font-size:15px;line-height:28.5px;color:#ddd}
.footer-rule{left:112px;top:280px;width:976px;height:1px;background:var(--line)}
.copyright{left:112px;top:301px;font-size:15px;color:#ddd}
.payments{left:802px;top:296px;display:flex;gap:4px}
.payments span{width:44px;height:28px;border-radius:3px;background:#e8e8e8}
</style>
</head>
<body>

<div class="abs promo-bar">Free shipping - Fast delivery - Largest in Norway</div>

<header class="abs site-header">
  <div class="abs brand"><span class="brand-mark"></span>Tagglunden.no</div>
  <nav class="abs main-nav">
    <span>Name tags</span><span>Minilappe</span><span>Ironing pads</span><span>Temalapper</span><span>MY ID</span><span>Drinking bottle</span><span>Contact Us</span>
  </nav>
  <div class="abs header-icons">
    <svg width="32" height="32" viewBox="0 0 32 32" fill="none" stroke="#111" stroke-width="1.8"><circle cx="16" cy="16" r="14"/><circle cx="16" cy="12" r="5" fill="#111"/><path d="M7 25c2-5 6-7 9-7s7 2 9 7" fill="#111"/></svg>
    <div style="position:relative">
      <svg width="32" height="30" viewBox="0 0 32 30" fill="none" stroke="#111" stroke-width="1.8"><path d="M1 3h5l4 16h16l4-11H8"/><circle cx="12" cy="25" r="2.2"/><circle cx="24" cy="25" r="2.2"/></svg>
      <span class="cart-count">0</span>
    </div>
  </div>
</header>

<section class="abs hero">
  <div class="abs hero-photo-tones" role="img" aria-label="Photo of a pencil-shaped cup with pencils, a feather pen and school supplies on a desk against a yellow wall"></div>
  <h1 class="abs hero-title">DESIGN YOUR OWN<br>NAME TAGS</h1>
  <p class="abs hero-text">Lorem ipsum dolor sit amet, consectetur adipiscg elit, sed do eiusmod tempor incididunt ut labore et dre magna aliqua.</p>
  <div class="abs hero-btn">MAKE NOW</div>
  <svg class="abs hero-arrow" style="left:62px" viewBox="0 0 38 38" fill="none" stroke="#fff" stroke-width="2"><path d="M22 11l-8 8 8 8"/></svg>
  <svg class="abs hero-arrow" style="left:1101px" viewBox="0 0 38 38" fill="none" stroke="#fff" stroke-width="2"><path d="M16 11l8 8-8 8"/></svg>
  <div class="abs hero-dots"><span></span><span></span><span></span><span></span></div>
</section>

<svg width="0" height="0" style="position:absolute"><defs><symbol id="star" viewBox="0 0 20 20"><path d="M10 1l2.7 6.1 6.6.6-5 4.4 1.5 6.5L10 15.2 4.2 18.6l1.5-6.5-5-4.4 6.6-.6z" fill="var(--star)"/></symbol></defs></svg>

<div class="abs rating-summary">
  <h3>Unique</h3>
  <div class="stars"><svg width="27" height="27"><use href="#star"/></svg><svg width="27" height="27"><use href="#star"/></svg><svg width="27" height="27"><use href="#star"/></svg><svg width="27" height="27"><use href="#star"/></svg><svg width="27" height="27"><use href="#star"/></svg></div>
  <p>Based on 12029 reviews</p>
  <div class="review-brand"><i></i>Reviewly</div>
</div>

<div class="abs review" style="left:340px">
  <div class="top"><div class="stars" style="margin:0"><svg width="20" height="20"><use href="#star"/></svg><svg width="20" height="20"><use href="#star"/></svg><svg width="20" height="20"><use href="#star"/></svg><svg width="20" height="20"><use href="#star"/></svg><svg width="20" height="20"><use href="#star"/></svg></div><small>2 Day ago</small></div>
  <h4>Lorem ipsum dolor sit amet,</h4>
  <p>Lorem ipsum doloconsectetur<br>adipiscing elit, sed do</p>
  <b>Kelly</b>
</div>
<div class="abs review" style="left:599px">
  <div class="top"><div class="stars" style="margin:0"><svg width="20" height="20"><use href="#star"/></svg><svg width="20" height="20"><use href="#star"/></svg><svg width="20" height="20"><use href="#star"/></svg><svg width="20" height="20"><use href="#star"/></svg><svg width="20" height="20"><use href="#star"/></svg></div><small>2 Day ago</small></div>
  <h4>Lorem ipsum dolor sit amet,</h4>
  <p>Lorem ipsum doloconsectetur<br>adipiscing elit, sed do</p>
  <b>Kelly</b>
</div>
<div class="abs review" style="left:852px">
  <div class="top"><div class="stars" style="margin:0"><svg width="20" height="20"><use href="#star"/></svg><svg width="20" height="20"><use href="#star"/></svg><svg width="20" height="20"><use href="#star"/></svg><svg width="20" height="20"><use href="#star"/></svg><svg width="20" height="20"><use href="#star"/></svg></div><small>2 Day ago</small></div>
  <h4>Lorem ipsum dolor sit amet,</h4>
  <p>Lorem ipsum doloconsectetur<br>adipiscing elit, sed do</p>
  <b>Kelly</b>
</div>

<div class="abs product-tile" style="left:112px;top:990px;background:linear-gradient(120deg,#7fc9ea 0%,#8fd0ee 48%,#f2b6c4 52%,#f7c7d3 100%)" role="img" aria-label="Photo of pacifiers on a blue and pink background">
  <div class="tile-caption"><h5>Mini Notes for Miniting</h5><p>The standard Lorem Ipsum</p><span class="tile-btn">MAKE NOW</span></div>
</div>
<div class="abs product-tile" style="left:442px;top:990px;background:linear-gradient(90deg,#e5b93a 0%,#f0e9da 45%,#e9dfcc 65%,#d6a73a 100%)" role="img" aria-label="Photo of a miniature white door with a flower pot against a yellow wall">
  <div class="tile-caption"><h5>Door Decoration</h5><p>The standard Lorem Ipsum</p><span class="tile-btn">MAKE NOW</span></div>
</div>
<div class="abs product-tile" style="left:772px;top:990px;background:linear-gradient(160deg,#f1efec 0%,#ebe6df 55%,#d9c7a6 100%)" role="img" aria-label="Photo of folded baby blankets and wooden toys on a dotted cloth">
  <div class="tile-caption"><h5>Large Name Tags</h5><p>The standard Lorem Ipsum</p><span class="tile-btn">MAKE NOW</span></div>
</div>
<div class="abs product-tile" style="left:112px;top:1301px;background:linear-gradient(180deg,#f0bcc6 0%,#eab3be 60%,#e3d6c8 100%)" role="img" aria-label="Photo of a pink nursery wall with shelf, toy bunny and cloud decorations">
  <div class="tile-caption"><h5>Wall Decoration</h5><p>The standard Lorem Ipsum</p><span class="tile-btn">MAKE NOW</span></div>
</div>
<div class="abs product-tile" style="left:442px;top:1301px;background:linear-gradient(90deg,#dcdcdc 0%,#f3c3b6 40%,#e8e8e8 75%,#d9d9d9 100%)" role="img" aria-label="Photo of a pink backpack next to a cup of pencils">
  <div class="tile-caption"><h5>Reflexes</h5><p>The standard Lorem Ipsum</p><span class="tile-btn">MAKE NOW</span></div>
</div>
<div class="abs product-tile" style="left:772px;top:1301px;background:linear-gradient(160deg,#ededed 0%,#e4e4e2 50%,#6b8f4a 80%,#e9e9e9 100%)" role="img" aria-label="Photo of a hand ironing a garment with a white steam iron">
  <div class="tile-caption"><h5>Ironing Pads</h5><p>The standard Lorem Ipsum</p><span class="tile-btn">MAKE NOW</span></div>
</div>

<div class="abs faq-photo" role="img" aria-label="Photo of boxed dolls lined up on a shop shelf"></div>
<section class="abs faq">
  <h2>FREQUENTLY ASKED QUESTIONS</h2>
  <div class="faq-item" style="top:131px">The standard Lorem Ipsum passage, used since the 1500s<svg width="22" height="22" stroke="#111" stroke-width="1.6"><path d="M11 1v20M1 11h20"/></svg></div>
  <div class="faq-item" style="top:190px">The standard Lorem Ipsum passage, used since the 1500s<svg width="22" height="22" stroke="#111" stroke-width="1.6"><path d="M11 1v20M1 11h20"/></svg></div>
  <div class="faq-item" style="top:249px">The standard Lorem Ipsum passage, used since the 1500s<svg width="22" height="22" stroke="#111" stroke-width="1.6"><path d="M11 1v20M1 11h20"/></svg></div>
  <div class="faq-item" style="top:308px">The standard Lorem Ipsum passage, used since the 1500s<svg width="22" height="22" stroke="#111" stroke-width="1.6"><path d="M11 1v20M1 11h20"/></svg></div>
  <div class="faq-item" style="top:367px">The standard Lorem Ipsum passage, used since the 1500s<svg width="22" height="22" stroke="#111" stroke-width="1.6"><path d="M11 1v20M1 11h20"/></svg></div>
</section>

<svg width="0" height="0" style="position:absolute"><defs><symbol id="quote" viewBox="0 0 26 20"><path d="M0 20V11C0 5 3 1 9 0l1 3C6 4 5 7 5 9h5v11zM15 20V11c0-6 3-10 9-11l1 3c-4 1-5 4-5 6h5v11z" fill="var(--teal)"/></symbol></defs></svg>

<div class="abs testimonial" style="left:111px">
  <svg width="24" height="19"><use href="#quote"/></svg>
  <p>Lorem ipsumlor sit amet, adipiscing elit, sed do eiusmod tempor incididunt ut labore et dolore magna aliqua. Quis ipsum suspendisse ultrices gravida. Risusommodo vr maecenas accumsan lcus vel facilisis.</p>
  <b>-John Smith</b>
</div>
<div class="abs testimonial" style="left:444px">
  <svg width="24" height="19"><use href="#quote"/></svg>
  <p>Lorem ipsumlor sit amet, adipiscing elit, sed do eiusmod tempor incididunt ut labore et dolore magna aliqua. Quis ipsum suspendisse ultrices gravida. Risusommodo vr maecenas accumsan lcus vel facilisis.</p>
  <b>-John Smith</b>
</div>
<div class="abs testimonial" style="left:778px">
  <svg width="24" height="19"><use href="#quote"/></svg>
  <p>Lorem ipsumlor sit amet, adipiscing elit, sed do eiusmod tempor incididunt ut labore et dolore magna aliqua. Quis ipsum suspendisse ultrices gravida. Risusommodo vr maecenas accumsan lcus vel facilisis.</p>
  <b>-John Smith</b>
</div>

<footer class="abs site-footer">
  <div class="abs footer-brand"><span class="brand-mark"></span>Tagglunden.no</div>
  <div class="abs socials"><span></span><span></span><span></span><span></span></div>
  <div class="abs footer-col" style="left:382px;top:62px">
    <h6>NAVIGATE</h6>
    <ul><li>Name tags</li><li>Name tags with familiar figures</li><li>Minilapper</li><li>Large name tags</li><li>Ironing pads</li><li>Other products</li></ul>
  </div>
  <div class="abs footer-col" style="left:676px;top:62px">
    <h6>POLICIES</h6>
    <ul><li>Shipping</li><li>Warranty</li><li>Terms &amp; Conditions</li><li>Returns</li><li>Privacy</li></ul>
  </div>
  <div class="abs footer-col" style="left:897px;top:62px">
    <h6>CUSTOMER CENTER</h6>
    <ul><li>Contact Us</li><li>Questions and answers</li><li>Satisfaction guarantee</li></ul>
  </div>
  <div class="abs footer-rule"></div>
  <div class="abs copyright">© 2021 Tagglunden.no. All Rights Reserved.</div>
  <div class="abs payments" aria-label="Accepted payment methods"><span></span><span></span><span></span><span></span><span></span><span></span></div>
</footer>

</body>
</html>
```